Compression Arm Sleeve Packaging

We are a seller of sports compression arm sleeves. Our arm sleeves are used by athletes in just about every sport. Baseball, football, & basketball make up our largest customer base. We are in need of a product packaging design as a Vector image.

We would like design to feature the following:
Front of package:
Name of product: Arm Sleeve, our logo, brand name, website address, center of package will need to have no content so sleeve can be seen through package.

Back of package: Size chart, website address, logo, brand name, product care:
Machine Wash <80F
Do Not Dry Clean
Do Not Iron
Do Not Bleach
Hang Dry

I have included a few samples of other arm sleeve brands packaging. The grivka package i like the "Grivka" scrolling across package, the qmotive package i like the different colors, although I would not want the same colors, The vantrelp i like that the name of company, & the item are in bold. I do not like the basketball player on the front.

Misc Notes. I have included a pic of our logo, as well as our brand name. The font used for our brand name can be changed. The color of logo can also be changed if needed. Also i have attached a picture of our website name. The measurement chart does not need to look exactly as one i posted.
Thank you for looking!!!

Target Market(s)

Athletes - Youth & adult

Font styles to use
Sans Serif

Requirements
Must have
• Brand Name - Tarnhollow Sports
• Website: tarnhollowsports.example
• Logo
• Measurement chart (back of package)
• Product Care (back of package)
• I am very open to colors. I see i have to choose color combos. Regardless of the colors i choose I am not a designer. Use your judgement on what you think works.
Nice to have
• Would like a package where the color really pops. If our arm sleeve package is placed beside 10 other arm sleeve brands packaging I want to be sure our package would be the one that stands out without being corny. Packaging should appeal to extreme athletes. Font - Our font is PLQ glintmark, however it is not my favorite. If you have something you think looks better go with it. Again if i was a designer you would not be reading this. Create a package that you think will stand out to extreme athletes, and at the same time the future extreme athletes.
Should not have
• Boring packaging.

```html
<!DOCTYPE html>
<html lang="en">
<head>
<meta charset="utf-8">
<title>Tarnhollow Sports – Arm Sleeve Package Front</title>
<link rel="stylesheet" href="https://fonts.googleapis.com/css2?family=Michroma&family=Saira:wght@300&display=swap">
<style>
  :root {
    --bg: #d6d6d6;
    --brand-red: #e00a17;
    --brand-red-deep: #c80913;
    --brand-green: #95c122;
    --window-white: #ffffff;
    --ink: #111111;
    --paper-text: #ffffff;
  }
  html, body {
    margin: 0;
    width: 1200px;
    height: 1200px;
    overflow: hidden;
    background: var(--bg);
  }
  .canvas {
    width: 1200px;
    height: 1200px;
    display: flex;
    align-items: center;
    justify-content: center;
  }
  .package-front {
    width: 667px;
    height: 945px;
    display: block;
  }
  .url { font-family: "Saira", sans-serif; font-weight: 300; fill: var(--ink); }
  .brand-name { font-family: "Michroma", sans-serif; fill: var(--ink); }
  .tagline, .product-name, .feature-note, .feature-label {
    font-family: "Michroma", sans-serif;
    fill: var(--paper-text);
  }
</style>
</head>
<body>
<main class="canvas">
  <svg class="package-front" viewBox="0 0 830 1176" xmlns="http://www.w3.org/2000/svg" aria-label="Tarnhollow Sports arm sleeve package, front">
    <defs>
      <linearGradient id="red-field" x1="0" y1="0" x2="1" y2="1">
        <stop offset="0" stop-color="var(--brand-red-deep)"/>
        <stop offset="0.5" stop-color="var(--brand-red)"/>
        <stop offset="1" stop-color="var(--brand-red-deep)"/>
      </linearGradient>
    </defs>

    <!-- clear window -->
    <rect class="window" width="830" height="1176" fill="var(--window-white)"/>

    <!-- top header band -->
    <path class="header-band" role="img" aria-label="Red header with hexagon texture"
          d="M0 0 H830 V190 C700 240 570 300 470 375 Q445 398 420 392 C300 368 150 332 0 300 Z"
          fill="url(#red-field)"/>

    <text class="url" x="412" y="88" font-size="32" text-anchor="middle">tarnhollowsports.example</text>

    <g class="brand-mark">
      <circle cx="410" cy="180" r="14" fill="var(--ink)"/>
      <text class="brand-name" x="410" y="245" font-size="30" text-anchor="middle">TARNHOLLOW</text>
      <text class="brand-name" x="410" y="285" font-size="30" text-anchor="middle">SPORTS</text>
    </g>

    <!-- bottom info band -->
    <path class="info-band"
          d="M0 530 C60 565 120 588 160 597 C290 630 390 655 430 664 Q445 667 465 658 C500 642 520 636 560 628 C660 606 760 570 830 542 V1176 H0 Z"
          fill="var(--brand-green)"/>

    <text class="tagline" x="415" y="772" font-size="30" text-anchor="middle" textLength="595" lengthAdjust="spacingAndGlyphs">★ATHLETES CHOICE★</text>
    <text class="product-name" x="415" y="845" font-size="78" text-anchor="middle" textLength="725" lengthAdjust="spacingAndGlyphs">ARM SLEEVE</text>
    <line class="divider" x1="94" y1="861" x2="726" y2="861" stroke="var(--paper-text)" stroke-width="2"/>
    <text class="feature-note" x="415" y="890" font-size="20" text-anchor="middle" textLength="506" lengthAdjust="spacingAndGlyphs">WITH OUR REINFORCED NON-SLIP</text>
    <text class="feature-note" x="415" y="918" font-size="20" text-anchor="middle" textLength="368" lengthAdjust="spacingAndGlyphs">SILICONE ELASTIC BAND</text>

    <g class="feature feature-compression">
      <circle cx="149" cy="1022" r="49" fill="var(--paper-text)"/>
      <path d="M128 990 L150 1046 M128 990 L124 1008 M128 990 L142 1000 M150 1046 L178 1030"
            stroke="var(--brand-green)" stroke-width="4" fill="none" stroke-linecap="round"/>
      <text class="feature-label" x="149" y="1105" font-size="15" text-anchor="middle">OVERALL</text>
      <text class="feature-label" x="149" y="1125" font-size="15" text-anchor="middle">COMPRESSION</text>
    </g>

    <g class="feature feature-moisture">
      <circle cx="420" cy="1022" r="49" fill="var(--paper-text)"/>
      <path d="M420 988 C428 1004 444 1020 444 1036 A24 24 0 0 1 396 1036 C396 1020 412 1004 420 988 Z" fill="var(--brand-green)"/>
      <path d="M408 1038 H432 L420 1050 Z" fill="var(--paper-text)"/>
      <text class="feature-label" x="420" y="1105" font-size="15" text-anchor="middle">MOISTURE</text>
      <text class="feature-label" x="420" y="1125" font-size="15" text-anchor="middle">WICKING MATERIAL</text>
    </g>

    <g class="feature feature-seam">
      <circle cx="690" cy="1022" r="49" fill="var(--paper-text)"/>
      <line x1="656" y1="1056" x2="724" y2="988" stroke="var(--brand-green)" stroke-width="1.5" stroke-dasharray="5 4"/>
      <text class="feature-label" x="690" y="1105" font-size="15" text-anchor="middle">FLAT SEAM</text>
      <text class="feature-label" x="690" y="1125" font-size="15" text-anchor="middle">TECHNOLOGY</text>
    </g>
  </svg>
</main>
</body>
</html>
```